first fantastic look and impression

We are looking for a concept for letterhead, business card, emailfooter and template for invoices or offers for our company in the consultation business.
The dancer is a symbol who we are: it looks simple, but there is a lot of hard work and many years of training in this movement. The look is also what we want: elegant, modern, strong, with a touch of extravaganza
Target Market(s)
Hotelbusiness , Consulting
Font styles to use
Sans Serif
Other font styles liked:
- please give us a option we are open
Requirements
Must have
- We are not typical consultants but sparring partners and coaches for the hotel and that should also be expressed in the design. Maybe there is an icon that supports the whole thing. We are more modern and bolder than our industry colleagues.
we are modern, fresh, agile, fast
Nice to have
- a icon

```html
<!DOCTYPE html>
<html lang="en">
<head>
<meta charset="utf-8">
<title>Hollenfeld+Partner – Business Card</title>
<link rel="stylesheet" href="https://fonts.googleapis.com/css2?family=Montserrat:wght@500;700&family=Roboto:wght@300;400&display=swap">
<style>
  :root {
    --page-bg: #151515;
    --card-bg: #fbfbfb;
    --ink: #1c1f2a;
    --ink-soft: #8a8a8a;
    --rule: #222222;
    --divider: #6b6b6b;
  }
  * { margin: 0; padding: 0; box-sizing: border-box; }
  html, body {
    width: 1200px; height: 900px; overflow: hidden;
    background: var(--page-bg);
  }
  .canvas {
    position: relative; width: 1200px; height: 900px;
    display: flex; align-items: center; justify-content: center;
  }
  .card {
    position: relative; width: 1000px; height: 572px;
    background: var(--card-bg);
    box-shadow: 0 20px 50px rgba(0,0,0,.6);
  }
  .card-frame { position: absolute; inset: 0; }
  .brand-wordmark {
    position: absolute; left: 40px; top: 212px; width: 430px;
    text-align: center;
    font-family: "Montserrat", sans-serif; font-weight: 500;
    font-size: 46px; letter-spacing: 1px; color: var(--ink);
  }
  .brand-wordmark .brand-sub { display: block; }
  .footer-name {
    position: absolute; left: 180px; top: 522px; width: 300px;
    text-align: center;
    font-family: "Montserrat", sans-serif; font-weight: 500;
    font-size: 17px; letter-spacing: 4px; color: var(--ink);
    text-transform: uppercase;
  }
  .divider {
    position: absolute; left: 510px; top: 150px; width: 1.5px; height: 300px;
    background: var(--divider);
  }
  .contact { position: absolute; left: 550px; top: 168px; }
  .contact-name {
    font-family: "Montserrat", sans-serif; font-weight: 700;
    font-size: 27px; color: var(--ink); text-transform: uppercase;
    letter-spacing: .3px;
  }
  .contact-role {
    font-family: "Montserrat", sans-serif; font-weight: 500;
    font-size: 22px; color: var(--ink-soft); margin-top: 2px;
  }
  .contact-list { list-style: none; margin-top: 22px; }
  .contact-list li {
    display: flex; align-items: center; gap: 12px;
    font-family: "Roboto", sans-serif; font-weight: 300;
    font-size: 23px; color: #555; line-height: 38px;
  }
  .contact-list svg { width: 20px; height: 20px; flex: none; fill: var(--ink); }
</style>
</head>
<body>
<main class="canvas">
  <article class="card">
    <svg class="card-frame" width="1000" height="572" viewBox="0 0 1000 572" aria-hidden="true">
      <g stroke="var(--rule)" stroke-width="2.5" fill="none">
        <line x1="36" y1="36" x2="964" y2="36"/>
        <line x1="964" y1="36" x2="964" y2="536"/>
        <line x1="36" y1="36" x2="36" y2="536"/>
        <line x1="36" y1="536" x2="175" y2="536"/>
        <line x1="485" y1="536" x2="964" y2="536"/>
      </g>
    </svg>

    <div class="brand-wordmark">Hollenfeld<span class="brand-sub">+Partner</span></div>
    <div class="footer-name">Hollenfeld+Partner</div>

    <div class="divider"></div>

    <section class="contact">
      <h1 class="contact-name">Lena Marwick</h1>
      <p class="contact-role">Managing Director</p>
      <ul class="contact-list">
        <li>
          <svg viewBox="0 0 24 24"><path d="M6.6 10.8a15 15 0 0 0 6.6 6.6l2.2-2.2c.3-.3.7-.4 1-.2 1.1.4 2.3.6 3.6.6.6 0 1 .4 1 1V20c0 .6-.4 1-1 1A17 17 0 0 1 3 4c0-.6.4-1 1-1h3.5c.6 0 1 .4 1 1 0 1.3.2 2.5.6 3.6.1.3 0 .7-.2 1z"/></svg>
          +43 555 014722
        </li>
        <li>
          <svg viewBox="0 0 24 24"><path d="M2 5h20v14H2z M3.5 6.5 12 13l8.5-6.5" fill="none" stroke="var(--ink)" stroke-width="2"/><path d="M2 5h20L12 12.5z"/></svg>
          info@hollenfeldpartner.com
        </li>
        <li>
          <svg viewBox="0 0 24 24"><g fill="none" stroke="var(--ink)" stroke-width="1.8"><circle cx="12" cy="12" r="9"/><ellipse cx="12" cy="12" rx="4" ry="9"/><line x1="3" y1="12" x2="21" y2="12"/></g></svg>
          www.hollenfeldpartner.com
        </li>
        <li>
          <svg viewBox="0 0 24 24"><path d="M12 2a7 7 0 0 0-7 7c0 5 7 13 7 13s7-8 7-13a7 7 0 0 0-7-7zm0 9.5A2.5 2.5 0 1 1 12 6.5a2.5 2.5 0 0 1 0 5z"/></svg>
          Lindenau/Austria
        </li>
      </ul>
    </section>
  </article>
</main>
</body>
</html>
```